Whitcombe Business Card Design

The name of the business is Dario Whitcombe, CPA LLC
The service that we offer is Accounting, Tax & Consulting Services. I need it to have the following items:
Dario Whitcombe, Principal
Phone Number
Email Address
Physical Address

I have attached the company logo, one in black and one in white. Please provide a design in black background and the other in white background. Please include "Accounting, Tax & Consulting Services". I want the business card to be clean and very professional.

```html
<!DOCTYPE html>
<html lang="en">
<head>
<meta charset="utf-8">
<title>Dario Whitcombe, CPA LLC – Business Card</title>
<link rel="stylesheet" href="https://fonts.googleapis.com/css2?family=Questrial&display=swap">
<style>
  :root {
    --backdrop: #4b4b4d;
    --card-light: #f1f1f1;
    --card-dark: #1c1c1d;
    --brand-red: #9b1c20;
    --ink-dark: #3b3b3d;
    --ink-grey: #8b8b8e;
    --ink-text: #4a4a4c;
    --ink-light: #ffffff;
    --ink-light-grey: #a9a9ac;
  }
  * { margin: 0; padding: 0; box-sizing: border-box; }
  html, body {
    width: 1200px; height: 1200px; overflow: hidden;
    background: var(--backdrop);
    font-family: "Questrial", sans-serif;
  }
  .canvas { position: relative; width: 1200px; height: 1200px; }
  .card {
    position: absolute; left: 228px; width: 744px; height: 426px;
    box-shadow: 0 6px 18px rgba(0,0,0,.45);
  }
  .card--front { top: 150px; background: var(--card-light); }
  .card--back { top: 640px; background: var(--card-dark); }

  .name-banner {
    position: absolute; left: 0; top: 62px; width: 292px; height: 66px;
    background: var(--brand-red);
    clip-path: polygon(0 0, 100% 0, 86% 100%, 0 100%);
    color: var(--ink-light); padding: 9px 0 0 45px;
  }
  .name-banner__name { font-size: 22px; letter-spacing: .3px; line-height: 1.1; }
  .name-banner__role { font-size: 15px; margin-top: 4px; }

  .firm { position: absolute; text-align: right; right: 42px; top: 70px; }
  .firm__name { font-size: 20px; color: var(--ink-dark); letter-spacing: .3px; }
  .firm__tagline { font-size: 13px; color: var(--ink-grey); letter-spacing: 1.6px; margin-top: 3px; }

  .brand-mark {
    position: absolute; display: flex; align-items: center; gap: 12px;
    transform: translate(-50%, -50%);
  }
  .brand-mark__square { width: 26px; height: 26px; background: var(--brand-red); flex: none; }
  .brand-mark__name { font-size: 24px; letter-spacing: 1.5px; }
  .card--front .brand-mark { left: 572px; top: 278px; }
  .card--front .brand-mark__name { color: var(--ink-dark); }
  .card--back .brand-mark { left: 372px; top: 140px; }
  .card--back .brand-mark__name { color: var(--ink-light); }

  .contact { position: absolute; left: 0; top: 172px; width: 305px; }
  .contact__row {
    display: flex; align-items: center;
    height: 50px; padding-left: 45px;
  }
  .contact__row--ruled { border-bottom: 1.5px solid var(--brand-red); }
  .contact__icon {
    width: 32px; height: 32px; border-radius: 50%;
    background: var(--brand-red); flex: none;
    display: flex; align-items: center; justify-content: center;
  }
  .contact__text { margin-left: 16px; font-size: 12px; color: var(--ink-text); line-height: 1.3; }

  .services {
    position: absolute; right: 28px; top: 378px;
    font-size: 17px; color: var(--brand-red); letter-spacing: .2px;
  }

  .back-lockup { position: absolute; left: 0; right: 0; top: 214px; text-align: center; }
  .back-lockup__name { font-size: 28px; color: var(--ink-light); letter-spacing: .4px; }
  .back-lockup__tagline { font-size: 17px; color: var(--ink-light-grey); letter-spacing: 2.2px; margin-top: 4px; }
</style>
</head>
<body>
<main class="canvas">

  <section class="card card--front" aria-label="Business card front, white background">
    <div class="name-banner">
      <p class="name-banner__name">DARIO WHITCOMBE</p>
      <p class="name-banner__role">Principal</p>
    </div>

    <div class="firm">
      <p class="firm__name">DARIO WHITCOMBE, CPA LLC</p>
      <p class="firm__tagline">CERTIFIED PUBLIC ACCOUNTANT</p>
    </div>

    <div class="brand-mark">
      <span class="brand-mark__square"></span>
      <span class="brand-mark__name">WHITCOMBE</span>
    </div>

    <div class="contact">
      <div class="contact__row contact__row--ruled">
        <span class="contact__icon">
          <svg width="16" height="16" viewBox="0 0 24 24" fill="none" stroke="#fff" stroke-width="1.8" stroke-linejoin="round">
            <path d="M5 3h4l2 5-2.5 1.5a11 11 0 0 0 6 6L16 13l5 2v4a2 2 0 0 1-2 2A16 16 0 0 1 3 5a2 2 0 0 1 2-2z"/>
          </svg>
        </span>
        <p class="contact__text">+31 (0) 10 5550142<br>+31 (0) 6 5550178</p>
      </div>
      <div class="contact__row contact__row--ruled">
        <span class="contact__icon">
          <svg width="16" height="16" viewBox="0 0 24 24" fill="none" stroke="#fff" stroke-width="1.8" stroke-linejoin="round">
            <rect x="3" y="5" width="18" height="14"/>
            <path d="M3 5l9 8 9-8"/>
          </svg>
        </span>
        <p class="contact__text">info@whitcombecpa.nl</p>
      </div>
      <div class="contact__row contact__row--ruled">
        <span class="contact__icon">
          <svg width="16" height="16" viewBox="0 0 24 24" fill="none" stroke="#fff" stroke-width="1.8" stroke-linejoin="round">
            <path d="M12 21s-7-6.5-7-12a7 7 0 0 1 14 0c0 5.5-7 12-7 12z"/>
            <circle cx="12" cy="9" r="2.5"/>
          </svg>
        </span>
        <p class="contact__text">Havenstraat 18<br>5011 AB Tilburg</p>
      </div>
      <div class="contact__row">
        <span class="contact__icon">
          <svg width="16" height="16" viewBox="0 0 24 24" fill="none" stroke="#fff" stroke-width="1.6">
            <circle cx="12" cy="12" r="9"/>
            <ellipse cx="12" cy="12" rx="4" ry="9"/>
            <path d="M3 12h18M5 7h14M5 17h14"/>
          </svg>
        </span>
        <p class="contact__text">www.whitcombecpa.nl<br>www.whitcombe-advies.nl</p>
      </div>
    </div>

    <p class="services">Accounting, Tax &amp; Consulting Services</p>
  </section>

  <section class="card card--back" aria-label="Business card back, black background">
    <div class="brand-mark">
      <span class="brand-mark__square"></span>
      <span class="brand-mark__name">WHITCOMBE</span>
    </div>
    <div class="back-lockup">
      <p class="back-lockup__name">DARIO WHITCOMBE, CPA LLC</p>
      <p class="back-lockup__tagline">CERTIFIED PUBLIC ACCOUNTANT</p>
    </div>
  </section>

</main>
</body>
</html>
```